Recruiting ad for Caregivers and Nurses

We need a few amazing, fun, catchy, creative recruiting ads for Caregivers and Nurses to care for homecare patients on the island of Oahu, in Hawaii. We are an in home care company called Palmer Homecare. Our care services are provided 24/7, so we need staff that can work days, nights, weekdays, weekends. We need catchy fun ads to entice caregivers and nurses to call our office to inquire about jobs available. Our patients age range is from babies to seniors. We need caregivers and nurses for basic patient care (bathing, dressing, ambulating, preparing meals, medication reminders, light housekeeping) and complex patients (oxygen, tube feeding, injections, vents, wound care). Here are some bullets to consider including:
*Full-time and Part-time Positions Available (days, nights, weekdays, weekends)
*Sign-On Bonus Programs Offered up to $500
*Refer a Friend Bonus Program
*Holiday Pay
*2 Health Plans to Choose from
*Island-Wide Locations
*All PPE Provided (masks, gloves, etc)
*401K Program
*Tuition Benefits

```html
<!DOCTYPE html>
<html lang="en">
<head>
<meta charset="utf-8">
<title>Palmer Homecare – Caregivers Recruiting Flyer</title>
<link rel="stylesheet" href="https://fonts.googleapis.com/css2?family=Marcellus&family=Arimo:wght@400;700&display=swap">
<style>
  :root {
    --stage: #8b8996;
    --teal-dark: #1d5d52;
    --teal-light: #a8dcd4;
    --salmon: #f29a80;
    --slate: #3e6473;
    --white: #ffffff;
  }
  * { box-sizing: border-box; margin: 0; padding: 0; }
  html, body { width: 1200px; height: 1200px; overflow: hidden; }
  body {
    background: var(--stage);
    position: relative;
    font-family: "Arimo", Arial, sans-serif;
  }
  .size-label {
    position: absolute; top: 66px; left: 0; width: 1200px;
    text-align: center; color: var(--white);
    font-weight: 700; font-size: 21px; letter-spacing: 0.5px;
  }
  .flyer {
    position: absolute; left: 217px; top: 130px;
    width: 767px; height: 992px; overflow: hidden;
    background: var(--white);
  }
  .flyer-shapes { position: absolute; inset: 0; width: 767px; height: 992px; }
  .flyer-title {
    position: absolute; top: 22px; right: 22px;
    font-family: "Marcellus", Georgia, serif; font-weight: 400;
    font-size: 76px; color: var(--teal-dark); line-height: 1;
  }
  .brand-name {
    position: absolute; left: 497px; top: 514px; width: 240px;
    text-align: center; color: var(--teal-dark);
    font-size: 26px; font-weight: 700; line-height: 32px;
    white-space: nowrap;
  }
  .positions { position: absolute; left: 24px; top: 592px; font-weight: 700; line-height: 1.1; }
  .positions-type { color: var(--salmon); font-size: 29px; }
  .positions-open { color: var(--teal-dark); font-size: 30px; letter-spacing: 0.3px; }
  .positions-rule {
    position: absolute; left: 0; top: 662px; width: 392px; height: 5px;
    background: var(--teal-light);
  }
  .benefits {
    position: absolute; left: 115px; top: 678px; width: 500px;
    list-style: none; text-align: center;
    color: var(--teal-dark); font-size: 15.5px; line-height: 20.4px; font-weight: 700;
  }
  .benefits li::before {
    content: ""; display: inline-block; width: 8px; height: 8px; border-radius: 50%;
    background: var(--salmon); margin-right: 7px; vertical-align: 1px;
  }
  .benefits .plain { font-weight: 400; }
  .care-duties { position: absolute; left: 14px; top: 877px; width: 320px; }
  .care-duties h2 {
    color: var(--salmon); font-size: 18px; font-weight: 700; line-height: 1.2;
  }
  .care-duties h2::before {
    content: ""; display: inline-block; width: 7px; height: 7px; border-radius: 50%;
    background: var(--salmon); margin-right: 6px; vertical-align: 3px;
  }
  .care-duties p {
    color: var(--white); font-size: 14.5px; line-height: 18.5px;
    margin-left: 17px; width: 290px;
  }
  .call-cta {
    position: absolute; right: 22px; top: 878px;
    font-family: "Marcellus", Georgia, serif; font-size: 36px; color: var(--teal-dark);
  }
  .phone {
    position: absolute; left: 434px; top: 924px;
    display: flex; align-items: center; gap: 11px;
    color: var(--white); font-size: 37px;
  }
  .phone-icon { width: 40px; height: 40px; }
</style>
</head>
<body>
  <div class="size-label">8.5 X 11'' (LETTER SIZE)</div>

  <main class="flyer">
    <svg class="flyer-shapes" viewBox="0 0 639 827" preserveAspectRatio="none">
      <defs>
        <linearGradient id="photoTone" x1="0" y1="0" x2="1" y2="1">
          <stop offset="0" stop-color="#e6e3a6"/>
          <stop offset="0.35" stop-color="#c9b07a"/>
          <stop offset="0.6" stop-color="#6f8fb3"/>
          <stop offset="1" stop-color="#9a6a3e"/>
        </linearGradient>
        <linearGradient id="headerTone" x1="0" y1="0" x2="1" y2="0">
          <stop offset="0" stop-color="#ffffff"/>
          <stop offset="0.5" stop-color="#e4f5f2"/>
          <stop offset="1" stop-color="#b5e2db"/>
        </linearGradient>
      </defs>

      <path role="img" aria-label="Photo: a smiling caregiver in blue scrubs sitting on a sofa with a laughing patient holding a glass of milk, in a bright living room"
            d="M0,0 H639 V540 C590,525 520,458 420,462 C250,470 120,420 0,332 Z" fill="url(#photoTone)"/>

      <path class="header-band" d="M40,0 H639 V222 C560,185 470,150 380,125 C260,92 120,60 40,0 Z" fill="url(#headerTone)"/>
      <path class="header-accent-left" d="M0,0 H40 C90,40 140,66 205,84 C130,80 60,52 0,22 Z" fill="var(--salmon)"/>
      <path class="header-accent-right" d="M380,125 C470,150 560,185 639,222 V262 C560,220 470,170 380,125 Z" fill="var(--salmon)"/>

      <path class="content-field" d="M0,332 C120,420 250,470 420,462 C520,458 590,525 639,540 V827 H0 Z"
            fill="var(--white)" stroke="var(--teal-light)" stroke-width="9"/>

      <path class="footer-band" d="M0,662 C120,652 230,690 320,758 C345,778 330,800 300,827 H0 Z" fill="var(--slate)"/>
      <path class="footer-stripe" d="M255,827 C350,758 460,698 639,662 V702 C470,722 380,772 300,827 Z" fill="var(--teal-light)"/>
      <path class="footer-call" d="M300,827 C380,772 470,722 639,702 V827 Z" fill="var(--salmon)"/>

      <circle class="brand-seal" cx="514" cy="442" r="102" fill="var(--white)" stroke="var(--salmon)" stroke-width="3"/>
    </svg>

    <h1 class="flyer-title">Caregivers</h1>

    <div class="brand-name">Palmer Homecare</div>

    <div class="positions">
      <div class="positions-type">FULL-TIME &amp; PART-TIME</div>
      <div class="positions-open">POSITIONS AVAILABLE</div>
    </div>
    <div class="positions-rule"></div>

    <ul class="benefits">
      <li>SIGN-ON BONUS PROGRAMS - <span class="plain">Offered up to $500</span></li>
      <li>REFER A FRIEND BONUS PROGRAM</li>
      <li>HOLIDAY PAY</li>
      <li>MEDICAL / DENTAL / VISION</li>
      <li><span class="plain">Island-Wide Locations</span></li>
      <li>All PPE Provided <span class="plain">(Masks, gloves, etc)</span></li>
      <li>401K PROGRAM</li>
      <li>FLEXIBLE SCHEDULE</li>
    </ul>

    <section class="care-duties">
      <h2>BASIC PATIENT CARE</h2>
      <p>(bathing, dressing, ambulating, preparing meals, medication reminders, light housekeeping)</p>
    </section>

    <div class="call-cta">Call Us</div>
    <div class="phone">
      <svg class="phone-icon" viewBox="0 0 40 40" aria-hidden="true">
        <circle cx="20" cy="20" r="19" fill="var(--slate)"/>
        <path d="M14 11c1-1 2-1 3 0l2 3c.6 1 .4 2-.4 2.6l-1.2 1c.8 2 2.6 4 4.8 5l1-1.2c.7-.8 1.7-1 2.6-.4l3 2c1 .7 1 2 0 3l-1.6 1.6c-1.4 1.4-4 1-7-1s-6-5.4-7.4-8.6c-1.2-2.8-.8-5 .4-6.4z" fill="var(--white)"/>
      </svg>
      <span>808-555-0142</span>
    </div>
  </main>
</body>
</html>
```